Internal Office Slogans / Motto / Vision Statements

Hi. We would like to put up some posters around the office with quotations such as -
-”Do what you do so well that they will want to see it again and bring their friends.”- Hollis Brandt
-Make your customers feel heard and understood. Make your customers feel respected and liked. Make your customers feel appreciated and helped. Understand that you can do none of these things unless you are sincere about them.
Terrence Oakley
- It’s a very predictable and satisfying phenomenon: whenever we get better, our customers do too.
Cal Pruett
-Catch people in the act of performing extraordinary customer service. Treat them like heroes. Tell their stories, far and wide.
Ned Farraday

The purpose of the posters is to reiterate our culture and vision within the organisation. They should be clean, crisp and eye catching, not gaudy or bright. Professional, bold and strong.

The company website and logo is at http://www.nexoraweb.com.au
Print size will be A1

Thanks for participating & looking forward to seeing your great work.
Updates

Hi All. . 

So to reiterate we are looking for one background design to be used for multiple quotes...  The list of quotes are as follows: 

Support and or Sales Office

 

Make your customers feel heard and understood.Make your customers feel respected and liked. Make your customers feelappreciated and helped. Understand that you can do none of these things unlessyou are sincere about them.

Terrence Oakley

 

Nothing liberates our greatness like the desireto help, the desire to serve

Dorothea Quill

 

It’s a very predictable and satisfying phenomenon:whenever we get better, our customers do too.

Cal Pruett

 

Success means we go to sleep at night knowingthat our talents and abilities were used in a way that served others.

Dorothea Quill.

 

The sole purpose of business is to create, serveand satisfy a customer, from beginning to end – and that’s everyone’s job.

Ned Farraday

 

We don’t celebrate closing a sale, we celebrateopening a relationship.

Rosalind Hext

I will never make you a promise – unless I giveyou a plan and procedure to make that promise possible.

Bo Tennant

 

Customers feel we take them for granted; onlyshow interest when we want an order; lavish our time on prospects; communicatemainly by invoice; are fixated on big accounts; drop them like hot potatoesonce we have the order; don’t follow through on promises; and satisfy our ownbureaucracy rather than their needs. We can do better than that, much better.

Alan P Merrow.

 

 

General and public area

 

Catch people in the act of performingextraordinary customer service. Treat them like heroes. Tell their stories, farand wide.

Ned Farraday

 

 

We see our customers as invited guests to aparty, and we are the hosts. It’s our job every day to make every importantaspect of the customer experience a little bit better." Carl Voight - Founder andCEO of Halverin

 

"If you do build a great experience,customers tell each other about that. Word of mouth is verypowerful."  Carl Voight

 

It's not a faithin technology. It's faith in people. Rick Palmer

 

“Being the richest man in the cemetery doesn’tmatter to me … Going to bed at night saying we’ve done something wonderful…that’s what matters to me.” Rick Palmer

 

The customer experience is the next competitivebattleground. Lance Morrow, CIO, Vantor Computers

 

”Do what you do so well that they will want tosee it again and bring their friends.”- Hollis Brandt

In the world of internet customer service, it isimportant to remember your competitor is only a mouse click away. FrankHolden (not sure who he is but like the quote).

The customer is why you go to work. If they goaway, you do, too. Peter Lindqvist (?)

 

MaybeSome for Sales or Build Team:

Quality is remembered long after the price is forgotten. Marzetti Family Slogan

```html
<!DOCTYPE html>
<html lang="en">
<head>
<meta charset="utf-8">
<title>Office Quote Poster – Terrence Oakley</title>
<link rel="stylesheet" href="https://fonts.googleapis.com/css2?family=Roboto+Condensed:wght@700&display=swap">
<style>
  :root {
    --page: #ffffff;
    --panel-dark: #000000;
    --panel-mid: #141414;
    --panel-light: #4a4a4a;
    --quote-ink: #ffffff;
    --accent-red: #e0141e;
  }
  html, body {
    margin: 0;
    padding: 0;
    width: 1200px;
    height: 900px;
    overflow: hidden;
    background: var(--page);
  }
  .poster {
    position: relative;
    width: 1200px;
    height: 900px;
    background: var(--page);
    font-family: "Roboto Condensed", "Arial Narrow", sans-serif;
  }
  .poster-panel {
    position: absolute;
    left: 37px;
    top: 52px;
    width: 1121px;
    height: 793px;
    background: linear-gradient(215deg, var(--panel-light) 0%, var(--panel-mid) 38%, var(--panel-dark) 100%);
  }
  .quote {
    position: absolute;
    left: 0;
    right: 0;
    top: 188px;
    margin: 0;
    text-align: center;
    color: var(--quote-ink);
    font-size: 45px;
    line-height: 64px;
    font-weight: 700;
    letter-spacing: 0;
  }
  .quote-author {
    position: absolute;
    left: 0;
    right: 0;
    top: 656px;
    margin: 0;
    text-align: center;
    color: var(--accent-red);
    font-size: 35px;
    line-height: 52px;
    font-weight: 700;
  }
  .brand {
    position: absolute;
    left: 67px;
    top: 797px;
    display: flex;
    align-items: center;
    gap: 4px;
    color: var(--quote-ink);
    font-size: 22px;
    line-height: 26px;
    font-weight: 700;
  }
  .brand-mark {
    width: 18px;
    height: 18px;
    background: var(--accent-red);
  }
</style>
</head>
<body>
  <main class="poster">
    <div class="poster-panel"></div>
    <blockquote class="quote">
      “Make your customers feel heard<br>
      and understood. Make you customers<br>
      feel respected and liked. Make your<br>
      customers feel appreciated and<br>
      helped. Understand that you can<br>
      do none of these things unless<br>
      you are sincere about them.”
    </blockquote>
    <p class="quote-author">Terrence Oakley</p>
    <div class="brand">
      <span class="brand-mark"></span>
      <span class="brand-name">Nexoraweb</span>
    </div>
  </main>
</body>
</html>
```